Q Linkora

Ned a new business card, need two designs one to be for communications and one to be for security.
Communications will have what we do on it which include:-
PABX systems
Data Cabling
Phone services
Fibre
Security
"your communications specialist in the Pilbara"
The Severity one will have on it:-
CCTV
Alarm
Access control
Security consulting
Communications services
"Your security partner in the Pilbara"
Target Market(s)
industry
Industry/Entity Type
Communications
Contact Information for Business Card
Marcus Delbrook
0427350912
marcus@qlinkora.com.au
www.qlinkora.com.au

```html
<!DOCTYPE html>
<html lang="en">
<head>
<meta charset="UTF-8">
<title>Q Linkora – Business Card</title>
<link href="https://fonts.googleapis.com/css2?family=Raleway:wght@400;600&family=PT+Sans:wght@400&display=swap" rel="stylesheet">
<style>
  :root {
    --backdrop: #1d1d1f;
    --card: #2f3034;
    --card-edge: #38393d;
    --orange: #f5a533;
    --white: #ffffff;
    --soft: #d6d6d6;
  }
  * { margin: 0; padding: 0; box-sizing: border-box; }
  html, body {
    width: 1200px; height: 900px; overflow: hidden;
    background: var(--backdrop);
  }
  .canvas { position: relative; width: 1200px; height: 900px; }
  .card {
    position: absolute; left: 331px; width: 543px; height: 315px;
    background: var(--card);
    border: 1px solid var(--card-edge);
    border-radius: 14px;
  }
  .card--front { top: 121px; }
  .card--back { top: 488px; }

  .brand {
    position: absolute; display: flex; align-items: center;
    font-family: "Raleway", sans-serif; font-weight: 600;
  }
  .brand__dot { border-radius: 50%; flex: none; }
  .brand--front { left: 36px; top: 126px; gap: 10px; color: var(--orange); font-size: 40px; }
  .brand--front .brand__dot { width: 16px; height: 16px; background: var(--orange); }
  .brand--back { left: 100px; top: 62px; gap: 14px; color: var(--white); font-size: 66px; }
  .brand--back .brand__dot { width: 22px; height: 22px; background: var(--white); }

  .contact { position: absolute; left: 283px; top: 116px; font-family: "Raleway", sans-serif; }
  .contact__name { font-size: 24px; font-weight: 400; color: var(--white); line-height: 1; }
  .contact__name span { color: var(--orange); }
  .contact__role { margin-top: 6px; padding-left: 2px; font-size: 16px; color: var(--soft); }
  .contact__details { margin-top: 24px; padding-left: 4px; font-size: 14px; color: var(--white); line-height: 19px; }

  .services {
    position: absolute; left: 177px; top: 178px; list-style: none;
    font-family: "PT Sans", sans-serif; font-size: 18px; line-height: 17px; color: var(--white);
  }
  .tagline {
    position: absolute; left: 0; right: 0; top: 257px; text-align: center;
    font-family: "PT Sans", sans-serif; font-size: 15px; color: var(--white);
  }
</style>
</head>
<body>
<main class="canvas">
  <section class="card card--front" aria-label="Card front">
    <div class="brand brand--front"><span class="brand__dot"></span>qlinkora</div>
    <div class="contact">
      <p class="contact__name">Marcus <span>Delbrook</span></p>
      <p class="contact__role">Managing Director</p>
      <p class="contact__details">marcus@qlinkora.com.au<br>0427 350 912</p>
    </div>
  </section>

  <section class="card card--back" aria-label="Card back">
    <div class="brand brand--back"><span class="brand__dot"></span>qlinkora</div>
    <ul class="services">
      <li>CCTV &nbsp;Alarm</li>
      <li>Access control</li>
      <li>Security consulting</li>
      <li>Communications services</li>
    </ul>
    <p class="tagline">"Your security partner in the Pilbara"</p>
  </section>
</main>
</body>
</html>
```